New Business Card Design for Manufacturing

We are an engineering/manufacturing company that offers Advanced machining/assembly/engineering services, as well as innovative products for the heavy duty engine cooling markets.

We are looking to get a new business card designed that is clean and modern looking, but still fits the wide range of technical/skilled work we do.

- We hope to use this design as the base for other design work in new Presentations, web, and print work.

Industry/Entity Type

Engineering

Contact Information for Business Card

Our preferred color of blue is (RGB) 22/71/159 but can vary slightly from that color. Our content will be our Logo and full company name (Vantrell Forge Works, Inc.), company address, name, job title, phone number with extension, cell number, fax number, website, and email address on the cards.
We'd like the full company name next to the logo, but we are open to other interpretations of that layout.
Preferably, we would like the back side to be clean with just our logo, and the front to contain all of the contact information.

Colors
2f74b4
0355a3
85abd2

Requirements
Must have
• - Logo, company name, needed content - We are open to interpretation beyond that.
• - Standard size business card.
• - Horizontal orientation.
• - Enough space for lengthy names / job titles (for example, a job title could read "Directory of Human Resources" or "V.P. of Governmental Affairs"). We need this to look clean, whether the title be short (CEO) or long (as described above).

```html
<!DOCTYPE html>
<html lang="en">
<head>
<meta charset="utf-8">
<title>Vantrell Forge Works – Business Card</title>
<link rel="stylesheet" href="https://fonts.googleapis.com/css2?family=Open+Sans:wght@400;600;700;800&display=swap">
<style>
  :root{
    --brand-blue:#0355a3;
    --deep-blue:#0b58a8;
    --sky-blue:#4db2e8;
    --pale-blue:#a9d3f2;
    --ink:#4a4a4a;
    --grey:#7a7a7a;
    --paper:#ffffff;
    --backdrop:#e4e6e9;
  }
  *{box-sizing:border-box;margin:0;padding:0}
  html,body{width:1200px;height:1000px;overflow:hidden}
  body{background:var(--backdrop);font-family:"Open Sans",Arial,sans-serif;position:relative}
  .card{position:absolute;left:320px;width:560px;height:320px;background:var(--paper);
        box-shadow:0 6px 18px rgba(0,0,0,.18);overflow:hidden}
  .card--front{top:130px}
  .card--back{top:550px}
  .card__art{position:absolute;inset:0}

  /* front */
  .company-name{position:absolute;left:30px;top:34px;color:var(--sky-blue);font-weight:800;
        font-size:15px;line-height:16px;text-transform:uppercase}
  .company-name small{font-size:8px}
  .wordmark{position:absolute;left:200px;top:22px;text-align:left}
  .wordmark__name{color:var(--brand-blue);font-weight:800;font-size:30px;line-height:32px;letter-spacing:.5px}
  .wordmark__tag{color:var(--brand-blue);font-weight:800;font-size:8px;letter-spacing:.6px;text-transform:uppercase}
  .person{position:absolute;left:0;right:0;top:96px;text-align:center;color:var(--ink)}
  .person__name{font-size:19px;letter-spacing:1.5px;font-weight:400}
  .person__title{font-size:10.5px;letter-spacing:1.2px;margin-top:2px}
  .address{position:absolute;left:180px;right:60px;top:145px;height:20px;color:var(--paper);
        font-size:11px;letter-spacing:1px;display:flex;align-items:center;justify-content:center;gap:8px}
  .contacts{position:absolute;list-style:none;color:var(--grey);font-size:11.5px;letter-spacing:1.2px}
  .contacts li{display:flex;align-items:center;gap:10px;height:22px}
  .contacts svg{width:12px;height:12px;fill:var(--ink)}
  .contacts--web{left:340px;top:192px}
  .contacts--phone{left:60px;top:226px}

  /* back */
  .logo-lockup{position:absolute;left:0;right:0;top:62px;text-align:center}
  .logo-lockup__name{color:var(--brand-blue);font-weight:800;font-size:68px;line-height:76px;letter-spacing:1px}
  .logo-lockup__tag{color:var(--grey);font-weight:800;font-size:17px;letter-spacing:.5px;text-transform:uppercase}
  .back-url{position:absolute;left:0;right:0;top:252px;text-align:center;color:var(--paper);font-size:15px}
</style>
</head>
<body>

<section class="card card--front" aria-label="Business card front">
  <svg class="card__art" viewBox="0 0 560 320" aria-hidden="true">
    <path d="M0 168 L560 168 L560 150 C560 190 540 184 470 184 L140 184 C110 184 105 168 80 168 Z" fill="var(--pale-blue)"/>
    <path d="M130 145 L560 145 L560 165 L160 165 C145 165 140 145 130 145 Z" fill="var(--sky-blue)"/>
    <path d="M360 94 L520 94 C545 94 548 110 548 130 L548 145 L400 145 C390 120 380 94 360 94 Z" fill="var(--pale-blue)" opacity=".7"/>
    <line x1="0" y1="168" x2="560" y2="168" stroke="var(--sky-blue)" stroke-width="2"/>
    <line x1="200" y1="92" x2="560" y2="80" stroke="var(--sky-blue)" stroke-width="1.5"/>
  </svg>

  <div class="company-name">Vantrell<br>Forge<br>Works <small>Inc</small></div>
  <div class="wordmark">
    <div class="wordmark__name">VANTRELL</div>
    <div class="wordmark__tag">Shaping What Runs Next</div>
  </div>

  <div class="person">
    <div class="person__name">NAME OF CEO</div>
    <div class="person__title">DIRECTORY OF HUMAN RESOURCES</div>
  </div>

  <div class="address">
    <svg width="10" height="13" viewBox="0 0 10 13"><path d="M5 0a5 5 0 0 0-5 5c0 3.5 5 8 5 8s5-4.5 5-8a5 5 0 0 0-5-5zm0 7a2 2 0 1 1 0-4 2 2 0 0 1 0 4z" fill="#fff"/></svg>
    YOUR COMPANY ADDRESS
  </div>

  <ul class="contacts contacts--web">
    <li><svg viewBox="0 0 12 12"><circle cx="6" cy="6" r="5.5"/><path d="M0.5 6h11M6 .5c-3 3-3 8 0 11M6 .5c3 3 3 8 0 11" stroke="#fff" stroke-width=".8" fill="none"/></svg>WEBSITE</li>
    <li><svg viewBox="0 0 12 12"><rect x="0" y="2" width="12" height="8"/><path d="M0 2l6 4.5L12 2" stroke="#fff" stroke-width="1" fill="none"/></svg>EMAIL ADDRESS</li>
  </ul>

  <ul class="contacts contacts--phone">
    <li><svg viewBox="0 0 12 12"><path d="M1 3c0-1.5 2-2.5 5-2.5S11 1.5 11 3v1H8V3H4v1H1zM2 5h8l1 6H1z"/></svg>PHONE NUMBER</li>
    <li><svg viewBox="0 0 12 12"><path d="M2.5 0.5l2 2.5-1.2 1.5c.8 1.8 2.4 3.4 4.2 4.2L9 7.5l2.5 2-1.5 2C5 11.5.5 7 .5 2z"/></svg>CELL NUMBER</li>
    <li><svg viewBox="0 0 12 12"><path d="M3 0h6v3H3zM0 4h12v5H9v3H3V9H0zM4 8v3h4V8z"/></svg>FAX NUMBER</li>
  </ul>
</section>

<section class="card card--back" aria-label="Business card back">
  <svg class="card__art" viewBox="0 0 560 320" aria-hidden="true">
    <line x1="455" y1="100" x2="560" y2="88" stroke="var(--sky-blue)" stroke-width="2"/>
    <line x1="0" y1="188" x2="110" y2="178" stroke="var(--sky-blue)" stroke-width="2"/>
    <path d="M0 320 L30 320 C60 250 70 232 150 226 L470 214 C520 212 545 225 560 250 L560 320 Z" fill="var(--deep-blue)"/>
  </svg>
  <div class="logo-lockup">
    <div class="logo-lockup__name">VANTRELL</div>
    <div class="logo-lockup__tag">Shaping What Runs Next</div>
  </div>
  <div class="back-url">www.website.com</div>
</section>

</body>
</html>
```